Income Tax and Accounting Brochure

I need a brochure using my new logo (file attached). I do tax work and accounting work. I am an EA (QFB Enrolled Agent - logo attached) and would like this incorporated into the brochure. I also have a MSA in Accounting. Please incorporate the text that I have provided in the brochure.
Updates

Need extra days to review

Target Market(s)

Tax Clients - both business and individuals

Industry/Entity Type

Accounting

Colors
0054AA
0677BA
7BADD7
CADEEF
E8F1F8

Requirements
Must have
• Use my logo and the QFB EA file in the brochure
Nice to have
• I would like to see a brochure that I can customize with my own text if possible.

```html
<!DOCTYPE html>
<html lang="en">
<head>
<meta charset="utf-8">
<title>MJH Accounting &amp; Consulting – Brochure</title>
<link rel="stylesheet" href="https://fonts.googleapis.com/css2?family=Open+Sans:wght@300;600;700&display=swap">
<style>
  :root{
    --brand-blue:#0054aa;
    --brand-mid:#0677ba;
    --brand-soft:#7badd7;
    --brand-pale:#cadeef;
    --brand-mist:#e8f1f8;
    --ink:#111111;
    --paper:#ffffff;
    --badge-tone:rgba(150,150,140,.16);
  }
  *{margin:0;padding:0;box-sizing:border-box}
  html,body{width:873px;height:1200px;overflow:hidden;background:var(--paper)}
  body{font-family:"Open Sans",sans-serif;color:var(--ink)}
  .brochure{position:relative;width:873px;height:1200px;overflow:hidden;background:var(--paper)}

  .hero{position:absolute;left:0;top:0;width:873px;height:395px}
  .hero-photo{position:absolute;inset:0;
    background:linear-gradient(100deg,#3f5670 0%,#6c7f94 35%,#9aa8b6 60%,#7d8c78 85%,#596a52 100%)}
  .hero-tint{position:absolute;inset:0;background:linear-gradient(180deg,rgba(30,60,100,.25),rgba(20,45,85,.5))}
  .hero-curve{position:absolute;left:0;top:0}
  .brand{position:absolute;left:10px;top:18px;display:flex;align-items:center;gap:10px}
  .brand-dot{width:52px;height:52px;border-radius:50%;background:var(--brand-blue)}
  .brand-name{font-weight:600;color:var(--brand-blue);font-size:14px;line-height:1.25;letter-spacing:.5px}
  .hero-title{position:absolute;left:30px;top:218px;color:var(--paper);font-weight:300;font-size:41px;line-height:50px}
  .hero-title .line1{padding-left:40px;display:block}
  .hero-title strong{font-weight:700}

  .content{position:absolute;left:0;top:0;width:873px}
  .badge-mark{position:absolute;left:60px;top:728px;width:570px;height:158px}
  .badge-mark .b1{position:absolute;left:0;top:0;width:290px;height:158px;background:var(--badge-tone)}
  .badge-mark .b2{position:absolute;left:320px;top:18px;width:250px;height:120px;background:var(--badge-tone)}

  .block{position:absolute;font-weight:600;font-size:13.6px;line-height:17.5px}
  h2,h3{position:absolute;font-weight:700;white-space:nowrap}
  .h-large{font-size:27px}
  .h-mid{font-size:20px}
  ul.gets{position:absolute;left:20px;top:884px;list-style:none;width:850px}
  ul.gets li{position:relative;padding-left:12px;font-weight:600;font-size:13.6px;line-height:17.5px;margin-bottom:12px}
  ul.gets li::before{content:"";position:absolute;left:0;top:7px;width:5px;height:5px;border-radius:50%;background:var(--ink)}
</style>
</head>
<body>
<div class="brochure">
  <header class="hero">
    <div class="hero-photo" role="img" aria-label="Photo of a young couple reviewing tax papers with an advisor on a sofa"></div>
    <div class="hero-tint"></div>
    <svg class="hero-curve" width="873" height="395" viewBox="0 0 873 395">
      <path d="M0 0 H322 C255 70 150 115 0 125 Z" fill="#ffffff"/>
    </svg>
    <div class="brand">
      <span class="brand-dot"></span>
      <span class="brand-name">MJH ACCOUNTING &amp;<br>CONSULTING, LLC</span>
    </div>
    <h1 class="hero-title"><span class="line1">income tax and</span>buisness <strong>consulting</strong></h1>
  </header>

  <section class="content">
    <div class="badge-mark" aria-hidden="true"><span class="b1"></span><span class="b2"></span></div>

    <h2 class="h-large" style="left:27px;top:413px">About Maren J Holloway, MSA EA (Principal)</h2>
    <p class="block" style="left:25px;top:465px">I have a Masters’Degree in accounting and am an QFB Enrolled Agent.I am also a LedgerBooks Advanced Certified<br>consltamt in both the online and desktop products including Enterprice and point of sale.I provide individual and<br>small business tax services,Accounting,bookkeeping,QFB representation,insurance audit representation,business<br>license assistance and more.</p>
    <p class="block" style="left:25px;top:551px">I have experience working with a wide &nbsp;variety of clients from the point where they first decide &nbsp;they want to start<br>a business.They are often unsure about what to do first -I have a lot of experience to offer you.</p>

    <h2 class="h-large" style="left:24px;top:611px">What a joy it is to watch success in action!</h2>
    <h3 class="h-mid" style="left:23px;top:665px">Tax preparation-why hire us?</h3>
    <p class="block" style="left:23px;top:702px">Preparing your own income tax return can be a task leaves you with more questions than answers.According to a<br>study &nbsp;released by the US goverment’s Federal Audit Bureau last year,most taxpayers (77% of 71 million taxpayers)<br>believe they benefited from using a professional tax preparer.</p>
    <p class="block" style="left:21px;top:767px">Whether we like it or not,today’s tax laws are so complicated that filing a relatively simple return can be confusing.It is just<br>too easy to overlook deductons and credits to which you are entitled.Even if you use a computer software program there’s<br>no substitute for the assistance of an experienced tax professional.</p>

    <h2 style="left:25px;top:838px;font-size:25px">Here’s What Your get...</h2>
    <ul class="gets">
      <li>Your tax return will be checked and rechecked by our computer software identifying potential problems the QFB may look<br>at more closely and reviewing the math to limit QFB contacts.</li>
      <li>Your tax return can be filed electronically so you will get a refund back quicker.</li>
      <li>Our staff will show you how to adjust your payroll withholding to get more money back each week.Why give the QFB an<br>interest free loan for up to 16 months.</li>
      <li>We will show you potential deductions to limit your tax liability for next year.In addition,we will give you a sheet of<br>commonly overlooked deductions to limit the following year’s tax liability.</li>
    </ul>

    <h2 style="left:30px;top:1057px;font-size:26px">Books a Mess:No Problem!</h2>
    <p class="block" style="left:33px;top:1108px">If you own a small bussiness and haven’t kept up your bookkeeping,dont’s worry.We can help you.We’ll prepare your<br>bookkeeping for the year,prepare a full schedule C,as well as your personal income tax return.Themn we’ll help you<br>set up an easy system that allows you to keep your books in tip-top shape next year.</p>
  </section>
</div>
</body>
</html>
```